Beacon Advisory Website

I currently have a website www.beaconadvisoryinc.com. We are a IT Consulting Company. Our website will pretty much tell out our services. I am looking to enhance my website and make it look more professional. Looking for very classy and Contemporary look and design for my website.

It Company

```html
<!DOCTYPE html>
<html lang="en">
<head>
<meta charset="utf-8">
<title>Beacon Advisory</title>
<link href="https://fonts.googleapis.com/css2?family=Roboto:wght@300;400;500;700&display=swap" rel="stylesheet">
<style>
:root{
  --blue:#1a9bd7;
  --navy:#1b3f7a;
  --text:#6b6f74;
  --heading:#3a3d40;
  --light:#f5f6f7;
  --line:#e2e4e6;
  --footer:#2a3338;
  --footer-text:#8b9499;
  --white:#ffffff;
}
*{margin:0;padding:0;box-sizing:border-box}
html,body{width:1200px;height:2332px;overflow:hidden}
body{font-family:'Roboto',Arial,sans-serif;color:var(--text);background:var(--white);position:relative}
.abs{position:absolute}
.topbar{top:0;left:0;width:1200px;height:4px;background:var(--blue)}
.header{top:4px;left:0;width:1200px;height:86px;background:var(--white)}
.brand{left:100px;top:22px;display:flex;align-items:center;gap:10px}
.brand-mark{width:40px;height:40px;background:var(--blue)}
.brand-name{font-size:22px;font-weight:700;color:var(--navy);letter-spacing:.5px;line-height:1}
.nav{top:38px;left:0;font-size:13px;color:#7c8086;text-transform:uppercase}
.nav span{position:absolute;white-space:nowrap}
.nav .active{color:var(--blue)}
.hero{top:90px;left:0;width:1200px;height:454px;background:linear-gradient(100deg,#eef3f7 0%,#dfe8ef 40%,#b7c6d3 70%,#8a9db0 100%)}
.hero-title{left:105px;top:140px;font-size:31px;font-weight:500;color:var(--blue)}
.hero-text{left:107px;top:190px;width:420px;font-size:15.5px;line-height:25px;color:#4f555b}
.hero-btn{left:107px;top:261px;width:199px;height:45px;border:1.5px solid var(--blue);color:var(--blue);font-size:15.5px;display:flex;align-items:center;justify-content:center}
.arrow{width:47px;height:47px;border-radius:50%;display:flex;align-items:center;justify-content:center}
.arrow-left{left:24px;top:204px;background:rgba(120,130,140,.55)}
.arrow-right{left:1127px;top:204px;border:2px solid #fff;background:rgba(40,50,60,.25)}
.section-title{left:0;width:1200px;text-align:center;font-size:28px;font-weight:300;color:var(--heading)}
.section-title b{font-weight:500;color:var(--navy)}
.welcome-text{left:210px;top:634px;width:780px;text-align:center;font-size:12.5px;line-height:21px}
.feature{top:698px;width:330px;text-align:center}
.feature-icon{width:86px;height:86px;border-radius:50%;border:2px solid var(--blue);margin:0 auto;display:flex;align-items:center;justify-content:center}
.feature-icon.filled{background:var(--navy);border-color:var(--navy)}
.feature h3{margin-top:20px;font-size:16px;font-weight:500;color:var(--blue)}
.feature.dark h3{color:var(--navy)}
.feature p{margin-top:12px;font-size:12px;line-height:21px;padding:0 20px}
.feature p a{color:var(--blue);text-decoration:none}
.vdivider{width:1px;height:170px;background:var(--line);top:712px}
.services{top:939px;left:0;width:1200px;height:607px;background:var(--light)}
.svc-card{width:349px;height:160px;background:var(--white);box-shadow:0 3px 8px rgba(0,0,0,.07)}
.svc-photo{width:160px;height:96px}
.svc-card h3{position:absolute;left:44px;top:20px;font-size:16px;font-weight:500;color:var(--blue);text-transform:uppercase}
.svc-card.dark h3{color:var(--navy)}
.svc-card p{position:absolute;left:46px;top:50px;width:285px;font-size:12px;line-height:21px;text-align:justify}
.svc-card .more{position:absolute;right:18px;bottom:22px;font-size:13px;color:var(--blue)}
.more-btn{left:491px;top:1448px;width:216px;height:52px;border:1.5px solid var(--navy);background:var(--white);color:var(--navy);font-size:16px;font-weight:500;display:flex;align-items:center;justify-content:center}
.col-title{font-size:28px;font-weight:300;color:var(--heading)}
.col-title b{font-weight:500;color:var(--navy)}
.avatar{left:100px;top:1648px;width:114px;height:114px;border-radius:50%;border:5px solid #fff;box-shadow:0 0 0 1px var(--line);background:linear-gradient(160deg,#e8d6a8,#c9c2b8)}
.quote-title{left:253px;top:1662px;font-size:17px;font-weight:500;color:var(--blue)}
.quote-role{left:255px;top:1692px;font-size:12px;color:#777}
.stars{left:254px;top:1716px;display:flex;gap:3px}
.quote{left:98px;top:1783px;width:428px;font-size:12px;line-height:21px;text-align:justify}
.dots{left:97px;top:1932px;display:flex;gap:5px}
.dots i{width:11px;height:11px;border-radius:50%;border:1.5px solid var(--blue)}
.dots i.on{border-color:var(--navy)}
.col-divider{left:538px;top:1593px;width:1px;height:355px;background:var(--line)}
.tabs{left:561px;top:1647px;width:539px;height:47px;display:flex;border:1px solid var(--line)}
.tabs span{flex:1;display:flex;align-items:center;justify-content:center;font-size:15.5px;color:#444;border-left:1px solid var(--line)}
.tabs span:first-child{border-left:none;background:var(--blue);color:#fff;position:relative}
.tabs span:first-child::after{content:"";position:absolute;bottom:-8px;left:50%;margin-left:-8px;border:8px solid transparent;border-bottom:0;border-top-color:var(--blue)}
.values{left:563px;top:1717px;width:537px;font-size:12px;line-height:21px}
.values .lead{font-size:13.5px;color:#444;font-weight:500;margin-bottom:10px}
.values h4{font-size:13.5px;color:#444;font-weight:500;margin:8px 0 6px}
.footer{top:1983px;left:0;width:1200px;height:349px;background:var(--footer)}
.f-brand{left:98px;top:40px;display:flex;align-items:center;gap:10px}
.f-brand .brand-mark{background:#5b666c}
.f-brand .brand-name{color:#8c969b;font-size:30px}
.f-about{left:98px;top:140px;width:390px;font-size:12.5px;line-height:20px;color:var(--footer-text)}
.f-phone{left:98px;top:218px;display:flex;align-items:center;gap:14px;font-size:17px;color:var(--blue)}
.f-vline{left:521px;top:42px;width:1px;height:180px;background:#3c464c}
.f-title{font-size:25px;font-weight:300;color:#c4cbcf}
.f-links span{position:absolute;font-size:12.5px;color:#c9d0d4;white-space:nowrap;padding-left:31px}
.f-links span::before{content:"";position:absolute;left:0;top:5px;width:6px;height:6px;border-radius:50%;background:var(--blue)}
.f-hline{left:40px;top:269px;width:1120px;height:1px;background:#3c464c}
.social{left:98px;top:294px;display:flex;gap:8px}
.social i{width:28px;height:28px;border-radius:50%;border:1px solid #7e888d}
.copy{right:97px;top:302px;font-size:12px;color:#9aa3a8}
</style>
</head>
<body>

<div class="abs topbar"></div>

<header class="abs header">
  <div class="abs brand">
    <div class="brand-mark"></div>
    <div class="brand-name">BEACON ADVISORY</div>
  </div>
  <nav class="abs nav">
    <span class="active" style="left:426px">Home</span>
    <span style="left:503px">Company</span>
    <span style="left:607px">Services</span>
    <span style="left:708px">Solutions</span>
    <span style="left:819px">Resources</span>
    <span style="left:934px">Career</span>
    <span style="left:1024px">Contact Us</span>
  </nav>
</header>

<section class="abs hero" role="img" aria-label="Photo of a hand joining two puzzle pieces against a soft light background">
  <h1 class="abs hero-title">BEACON ADVISORY</h1>
  <p class="abs hero-text">Beacon Advisory maintains a global presence, aggressively recruiting expertly qualified IT &amp; Management Professionals</p>
  <div class="abs hero-btn">READ MORE HERE</div>
  <div class="abs arrow arrow-left"><svg width="14" height="14" viewBox="0 0 14 14"><path d="M9 2 4 7l5 5" fill="none" stroke="#fff" stroke-width="1.8"/></svg></div>
  <div class="abs arrow arrow-right"><svg width="14" height="14" viewBox="0 0 14 14"><path d="M5 2l5 5-5 5" fill="none" stroke="#fff" stroke-width="1.8"/></svg></div>
</section>

<h2 class="abs section-title" style="top:584px">WELCOME TO <b>BEACON ADVISORY</b></h2>
<p class="abs welcome-text">Today's IT market is a dynamic, fast-paced industry, with ever-increasing demands. Meeting these demands for over 25 years, Beacon Advisory maintains a global presence, aggressively recruiting expertly qualified IT and Management Professionals from around the world and cultivating key partnerships</p>

<div class="abs feature" style="left:84px">
  <div class="feature-icon"><svg width="50" height="36" viewBox="0 0 50 36" fill="none" stroke="#1a9bd7" stroke-width="2"><path d="M20 4a14 12 0 1 0 0 24h4l-2 5 7-6a14 12 0 0 0-9-23z"/><path d="M32 8a12 10 0 1 1 0 20h-3l2 4-6-5"/></svg></div>
  <h3>IT CONSULTING</h3>
  <p>Information technology should improve business results. Veltra helps companies make sure it does. We look at IT issues strategically, in the broader <a>[ Read More ]</a></p>
</div>
<div class="abs vdivider" style="left:432px"></div>
<div class="abs feature dark" style="left:436px">
  <div class="feature-icon filled"><svg width="44" height="44" viewBox="0 0 44 44" fill="none" stroke="#fff" stroke-width="2"><circle cx="22" cy="22" r="15"/><path d="M22 12l-8 18h16z"/></svg></div>
  <h3>STAFF AUGMENTATION</h3>
  <p>Information technology should improve business results. Veltra helps companies make sure it does. We look at IT issues strategically, in the broader <a style="color:#1b3f7a">[ Read More ]</a></p>
</div>
<div class="abs vdivider" style="left:768px"></div>
<div class="abs feature" style="left:789px">
  <div class="feature-icon"><svg width="46" height="46" viewBox="0 0 46 46" fill="none" stroke="#1a9bd7" stroke-width="3"><circle cx="23" cy="23" r="8"/><circle cx="23" cy="23" r="15" stroke-dasharray="6 4"/></svg></div>
  <h3>OFFSHORE</h3>
  <p>Information technology should improve business results. Veltra helps companies make sure it does. We look at IT issues strategically, in the broader <a>[ Read More ]</a></p>
</div>

<section class="abs services"></section>
<h2 class="abs section-title" style="top:980px">OUR <b>SERVICE</b></h2>

<div class="abs svc-card" style="left:228px;top:1044px">
  <h3>Technology</h3>
  <p>Beacon Advisory Training programs are perfect for individuals to enhance their careers. Our hands-on practical and interactive programs use real time</p>
  <span class="more">[ Read More ]</span>
</div>
<div class="abs svc-photo" role="img" aria-label="Photo of a finger touching a digital world map display" style="left:98px;top:1054px;height:96px;background:linear-gradient(135deg,#2b3036,#6d7680)"></div>

<div class="abs svc-card dark" style="left:754px;top:1044px">
  <h3 style="color:#1a9bd7">Business</h3>
  <p>Our Offshore development model has a unique distinction of providing efficient software solutions with cost and quality advantage, using state-of-the-art</p>
  <span class="more">[ Read More ]</span>
</div>
<div class="abs svc-photo" role="img" aria-label="Photo of two business people shaking hands" style="left:623px;top:1054px;background:linear-gradient(135deg,#c9d3dc,#4a5866)"></div>

<div class="abs svc-card dark" style="left:228px;top:1246px">
  <h3>Application Developement</h3>
  <p>Drawing on our experience in all major industries, we develop solutions that meet the most challenging IT problems. Our team follows</p>
  <span class="more" style="color:#1b3f7a">[ Read More ]</span>
</div>
<div class="abs svc-photo" role="img" aria-label="Photo of hands typing on a laptop keyboard" style="left:98px;top:1256px;height:140px;background:linear-gradient(135deg,#d8dde2,#7d8791)"></div>

<div class="abs svc-card" style="left:754px;top:1246px">
  <h3>Enterprise Integration</h3>
  <p>As organizations work to achieve and sustain competitive advantage, the ability for IT departments to demonstrate their value and deliver results</p>
  <span class="more">[ Read More ]</span>
</div>
<div class="abs svc-photo" role="img" aria-label="Photo of a team meeting in a bright office" style="left:623px;top:1256px;height:140px;background:linear-gradient(135deg,#cfd8e0,#5c6b78)"></div>

<div class="abs more-btn">VIEW MORE SERVICE</div>

<h2 class="abs col-title" style="left:98px;top:1590px">OUR <b>TESTIMONIAL</b></h2>
<div class="abs avatar" role="img" aria-label="Portrait photo of the client"></div>
<div class="abs quote-title">Northgate Finance is Great Firm</div>
<div class="abs quote-role">Daniel Marsh ( CEO &amp; Founder )</div>
<div class="abs stars">
  <svg width="88" height="16" viewBox="0 0 88 16" fill="#f2b705"><path id="st" d="M8 0l2.4 5 5.6.7-4 3.8 1 5.5L8 12.4 3 15l1-5.5-4-3.8L5.6 5z"/><use href="#st" x="18"/><use href="#st" x="36"/><use href="#st" x="54"/><use href="#st" x="72"/></svg>
</div>
<p class="abs quote">" It is a long established fact that a reader will be distracted by the readable content of a page when looking at its layout. The point of using Lorem Ipsum is that it has a more-or-less normal distribution of letters, as opposed to using 'Content here, content here', making it look like readable English. Many desktop publishing packages and web page editors now use Lorem Ipsum as their default model text, and a search for 'lorem ipsum' will uncover "</p>
<div class="abs dots"><i></i><i></i><i></i><i></i><i class="on"></i></div>

<div class="abs col-divider"></div>

<h2 class="abs col-title" style="left:561px;top:1590px">OUR <b>COMPANY VALUES</b></h2>
<div class="abs tabs"><span>OUR VISION</span><span>OUR MISSION</span><span>QUALITY FOCUS</span></div>
<div class="abs values">
  <p class="lead">Be #1 in Information Technology Consulting Services by delighting our customers!</p>
  <h4>We will:</h4>
  <p>Delivers highest level of Quality Consultants and services for the lowest Cost of Ownership Forge Client relationships to better understand and respond to their business needs Develop, challenge, empower and recognize our employees to promote an environment of enthusiastic achievement</p>
  <h4 style="margin-top:14px">Our Values :</h4>
  <p>Beacon Advisory has been governed by its core values. They shape the culture and define the character of our company. They guide how we behave and make decisions.Attracting and developing the best talent for our business, stretching our people and developing a "can do" attitude.</p>
</div>

<footer class="abs footer">
  <div class="abs f-brand">
    <div class="brand-mark" style="width:52px;height:52px"></div>
    <div class="brand-name">BEACON ADVISORY</div>
  </div>
  <p class="abs f-about">Today's IT market is a dynamic, fast-paced industry, with ever-increasing demands. Meeting these demands for over 25 years, Beacon Advisory maintains a global presence, aggressively recruiting expertly</p>
  <div class="abs f-phone">
    <svg width="20" height="20" viewBox="0 0 20 20" fill="#1a9bd7"><path d="M4 1l3 4-2 2c1 3 4 6 7 7l2-2 4 3-2 4C8 19 1 12 1 3z"/></svg>
    Phone: +1 (555) 014 2290
  </div>
  <div class="abs f-vline"></div>

  <h3 class="abs f-title" style="left:559px;top:36px">Quick Links</h3>
  <div class="f-links">
    <span style="left:561px;top:98px">Home</span>
    <span style="left:561px;top:136px">Company</span>
    <span style="left:561px;top:175px">Services</span>
    <span style="left:561px;top:214px">Solutions</span>
    <span style="left:681px;top:98px">Resources</span>
    <span style="left:681px;top:136px">Career</span>
    <span style="left:681px;top:175px">Contact Us</span>
  </div>

  <h3 class="abs f-title" style="left:828px;top:36px">Our Services</h3>
  <div class="f-links">
    <span style="left:831px;top:98px">Technology</span>
    <span style="left:831px;top:136px">Offshore</span>
    <span style="left:831px;top:175px">Application</span>
    <span style="left:831px;top:214px">Developement</span>
    <span style="left:966px;top:98px">Enterprise</span>
    <span style="left:966px;top:136px">Integration</span>
    <span style="left:966px;top:175px">IT Consulting</span>
  </div>

  <div class="abs f-hline"></div>
  <div class="abs social"><i></i><i></i><i></i><i></i><i></i></div>
  <div class="abs copy">Copyrights@2016 Company Name, all Rights Reserved</div>
</footer>

</body>
</html>
```